In need of an AWESOME website for our Water Re-filling Store

The project is to design a website for our retail store front with the website www.quellbrookfillhouse.com. Currently if you go to that site it redirects you to our other site www.quellbrookbottleworks.com which is just our water bottle website. So, I need a new website created for www.quellbrookfillhouse.com (retail storefront)
Use our Squarespace to create a site with pages to help educate, tell about us, link to our water bottle brand site that is already created with Squarespace, and show the family and community aspects that we believe in. Our current water bottle website is www.quellbrookbottleworks.com for reference
We also sell hydration products, especially PRZQ products and have access to digital media through our PRZQ dealer site. we sell bottles, dispensers and other supplies for water refilling customers. We sell Ice as well.

Target Market(s)

Local residents looking to fill up their 1-5 gallon water jugs

Industry/Entity Type

Alkaline and Purified Water Retail Re-filling Store

Coding

Coded - Design and coding required

Font styles to use
Serif
Sans Serif

Colors
0054AA
0677BA
7BADD7
CADEEF
E8F1F8

Requirements
Must have
• pictures of our family in the about us section and pictures of our store inside and out.

```html
<!DOCTYPE html>
<html lang="en">
<head>
<meta charset="utf-8">
<title>Quellbrook Fill House</title>
<link href="https://fonts.googleapis.com/css2?family=Roboto:wght@400;500;700&family=Arimo:wght@400;700&display=swap" rel="stylesheet">
<style>
:root{
  --blue-deep:#0B3F98;
  --blue:#0054AA;
  --blue-mid:#0677BA;
  --blue-soft:#7BADD7;
  --blue-pale:#CADEEF;
  --blue-wash:#E3ECF6;
  --ink:#1a1a1a;
  --white:#ffffff;
}
*{box-sizing:border-box;margin:0;padding:0}
html,body{width:1200px;height:3548px;overflow:hidden}
body{position:relative;background:var(--white);font-family:"Arimo",Arial,sans-serif;color:var(--ink)}
.abs{position:absolute}
.heading{font-family:"Roboto",Arial,sans-serif;font-weight:700;color:var(--blue-deep);line-height:1}
.body-copy{font-size:12.5px;line-height:1.35}
.btn{position:absolute;display:flex;align-items:center;justify-content:center;border-radius:22px;font-family:"Roboto",Arial,sans-serif;font-size:13.5px;color:var(--white);background:var(--blue-deep)}
.photo{position:absolute}

/* header */
.site-header{left:0;top:0;width:1200px;height:83px;background:var(--white);z-index:3}
.brand-badge{left:93px;top:4px;width:134px;height:134px;border-radius:50%;background:var(--white);z-index:4;display:flex;align-items:center;justify-content:center;border:7px solid var(--blue-deep);box-shadow:0 0 0 5px var(--white)}
.brand-name{font-family:"Roboto",Arial,sans-serif;font-weight:500;color:var(--blue);font-size:13px;text-align:center;line-height:1.15}
.nav{top:36px;font-family:"Roboto",Arial,sans-serif;font-size:13px;color:var(--ink)}
.nav.active{color:var(--blue)}
.social{top:35px;width:12px;height:12px;border-radius:50%;background:var(--blue-deep)}

/* hero */
.hero{left:0;top:83px;width:1200px;height:612px;background:linear-gradient(180deg,#5a4a38 0%,#6d5a45 40%,#9aa0aa 70%,#c9ced8 100%)}
.hero-title{left:111px;top:312px;font-family:"Roboto",Arial,sans-serif;font-weight:700;font-size:43px;color:var(--white)}
.hero-sub{left:111px;top:373px;width:620px;font-family:"Roboto",Arial,sans-serif;font-size:20px;line-height:1.27;color:var(--white)}
.btn-light{left:111px;top:439px;width:155px;height:38px;background:var(--white);color:var(--blue-deep);font-size:16px}
.btn-hero{left:278px;top:443px;width:140px;height:38px;background:var(--blue);font-size:16px}

/* mission band */
.mission{left:0;top:695px;width:1200px;height:161px;background:var(--blue-deep)}
.mission-name{left:115px;top:750px;font-family:"Roboto",Arial,sans-serif;font-weight:700;font-size:26px;line-height:1.05;color:var(--white)}
.mission-text{left:303px;top:746px;width:800px;font-size:15px;line-height:1.33;color:var(--white)}

/* best seller */
.section-title{font-size:62px}
.product-frame{border:2px solid var(--blue-deep)}
.caption{font-size:13.5px}

/* about */
.about{left:0;top:1297px;width:1200px;height:598px;background:var(--blue-wash)}

/* services */
.service-label{font-family:"Roboto",Arial,sans-serif;font-size:20px;font-weight:500}

/* footer */
.footer{left:0;top:3273px;width:1200px;height:275px;background:var(--blue-wash)}
.footer-badge{left:111px;top:3305px;width:117px;height:117px;border-radius:50%;border:5px solid var(--blue-deep);background:var(--white);display:flex;align-items:center;justify-content:center}
.footer-link{left:288px;font-size:13px;font-weight:700;color:var(--ink)}
.signup-note{left:714px;top:3323px;font-size:12px;font-weight:700}
.email-field{left:714px;top:3358px;width:180px;height:38px;background:var(--white);font-size:10px;color:#c4c4c4;padding:13px 0 0 18px}
.btn-signup{left:940px;top:3358px;width:111px;height:38px;border-radius:0;font-size:13px;font-weight:700;background:var(--blue-deep)}
.copyright{left:938px;top:3471px;font-size:12px}
</style>
</head>
<body>

<header class="abs site-header"></header>
<div class="abs brand-badge"><div class="brand-name">Quellbrook<br>Fill House</div></div>
<span class="abs nav active" style="left:354px">Home</span>
<span class="abs nav" style="left:424px">About Us</span>
<span class="abs nav" style="left:509px">Products</span>
<span class="abs nav" style="left:594px">Contact Us</span>
<span class="abs social" style="left:1001px" aria-hidden="true"></span>
<span class="abs social" style="left:1043px" aria-hidden="true"></span>
<span class="abs social" style="left:1086px" aria-hidden="true"></span>

<section class="abs hero" role="img" aria-label="Store owners standing behind rows of branded water bottles in the stock room"></section>
<h1 class="abs hero-title">Refresh. Rehydrate. Recharge.</h1>
<p class="abs hero-sub">Your neighborhood hydration destination for premium alkaline water, custom drinks, and refill solutions.</p>
<a class="btn btn-light">Visit Us Today</a>
<a class="btn btn-hero">Refill &amp; Save</a>

<section class="abs mission"></section>
<div class="abs mission-name">Quellbrook<br>Fill House</div>
<p class="abs mission-text">Quellbrook Fill House was created with one goal: make clean, high-quality hydration accessible to everyone. We believe water should do more than just quench thirst—it should support your lifestyle.</p>

<h2 class="abs heading section-title" style="left:102px;top:918px">Best Seller</h2>
<p class="abs body-copy" style="left:102px;top:997px;width:320px">Lorem ipsum dolor sit amet, consectetur adipiscing elit, sed do eiusmod tempor incididunt ut labore et dolore magna aliqua. Quis ipsum suspendisse ultrices gravida. Risus commodo viverra maecenas accumsan lacus vel facilisis.</p>
<a class="btn" style="left:102px;top:1100px;width:155px;height:38px">Shop Best Sellers</a>

<div class="photo product-frame" style="left:483px;top:920px;width:192px;height:267px;background:linear-gradient(180deg,#6e7a7a,#2e3a38 60%,#7bbcb0)" role="img" aria-label="Cooler shelves stocked with PRZQ drink mix cans"></div>
<div class="photo product-frame" style="left:695px;top:920px;width:191px;height:267px;background:linear-gradient(180deg,#b9c6da,#2b2b2f 45%,#f1f1f1)" role="img" aria-label="Wall display of water bottles and jug dispensers"></div>
<div class="photo product-frame" style="left:906px;top:920px;width:191px;height:267px;background:linear-gradient(90deg,#6e1d2a,#b32635 45%,#e5c321 60%,#d9a417)" role="img" aria-label="Two bottles of cold pressed juice"></div>
<span class="abs caption" style="left:486px;top:1204px">PRZQ Products</span>
<span class="abs caption" style="left:695px;top:1206px">Bottles</span>
<span class="abs caption" style="left:907px;top:1204px">Pressed Juice</span>

<section class="abs about"></section>
<div class="photo" style="left:102px;top:1370px;width:402px;height:420px;background:linear-gradient(180deg,#b8b4a8,#c9bda8 45%,#8c7f70)" role="img" aria-label="Family portrait of the owners and their children on the beach"></div>
<h2 class="abs heading section-title" style="left:560px;top:1430px">About Us</h2>
<p class="abs body-copy" style="left:561px;top:1511px;width:520px">Lorem ipsum dolor sit amet, consectetur adipiscing elit, sed do eiusmod tempor incididunt ut labore et dolore magna aliqua. Quis ipsum suspendisse ultrices gravida. Risus commodo viverra maecenas accumsan lacus vel facilisis.</p>
<p class="abs body-copy" style="left:561px;top:1579px;width:520px">Lorem ipsum dolor sit amet, consectetur adipiscing elit, sed do eiusmod tempor incididunt ut labore et dolore magna aliqua. Quis ipsum suspendisse ultrices gravida. Risus commodo viverra maecenas accumsan lacus vel facilisis.</p>
<a class="btn" style="left:561px;top:1654px;width:120px;height:37px">Learn More</a>

<h2 class="abs heading section-title" style="left:0;top:1968px;width:1200px;text-align:center">What we do</h2>
<p class="abs body-copy" style="left:340px;top:2054px;width:520px;text-align:center">Lorem ipsum dolor sit amet, consectetur adipiscing elit, sed do eiusmod tempor incididunt ut labore et dolore magna aliqua. Quis ipsum suspendisse ultrices gravida. Risus commodo viverra maecenas accumsan lacus vel facilisis. Lorem ipsum dolor sit amet, consectetur adipiscing elit.</p>
<a class="btn" style="left:540px;top:2137px;width:120px;height:36px">Our Products</a>

<div class="photo" style="left:102px;top:2210px;width:318px;height:343px;background:linear-gradient(180deg,#e2c2e0,#d8b3d8 60%,#a43aa0 85%,#d9b3d6)" role="img" aria-label="Purple gradient water bottles on a display stand"></div>
<div class="photo" style="left:441px;top:2210px;width:317px;height:343px;background:linear-gradient(180deg,#dde9f6,#a9c5ec 50%,#dde9f6)" role="img" aria-label="Five gallon refill water jug"></div>
<div class="photo" style="left:779px;top:2210px;width:318px;height:343px;background:linear-gradient(135deg,#dcdcdc,#c4c4c4 45%,#2a2a2a 55%,#d0d0d0)" role="img" aria-label="Matte black insulated water bottle"></div>
<span class="abs service-label" style="left:104px;top:2565px">Water Bottle</span>
<span class="abs service-label" style="left:444px;top:2568px">Water Refilling</span>
<span class="abs service-label" style="left:786px;top:2568px">Water Bottle</span>

<div class="photo" style="left:0;top:2675px;width:600px;height:598px;background:linear-gradient(180deg,#c8ab83,#b89a73 45%,#2c2c2e 70%,#9a9a9a)" role="img" aria-label="Outside of the store with a coming soon banner over the entrance"></div>
<div class="photo" style="left:600px;top:2675px;width:600px;height:598px;background:linear-gradient(135deg,#4a4a4a,#c23a3a 30%,#6b6b6b 55%,#1c2a55 80%,#d8d4c8)" role="img" aria-label="Inside the store with apparel racks and a product display table"></div>

<footer class="abs footer"></footer>
<div class="abs footer-badge"><div class="brand-name" style="font-size:12px">Quellbrook<br>Fill House</div></div>
<span class="abs footer-link" style="top:3324px">Home</span>
<span class="abs footer-link" style="top:3345px">About Us</span>
<span class="abs footer-link" style="top:3366px">Products</span>
<span class="abs footer-link" style="top:3387px">Contact Us</span>
<span class="abs signup-note">Sign up to receive news and updates.</span>
<div class="abs email-field">Email Address</div>
<a class="btn btn-signup">Sign Up</a>
<span class="abs social" style="left:117px;top:3459px" aria-hidden="true"></span>
<span class="abs social" style="left:158px;top:3459px" aria-hidden="true"></span>
<span class="abs social" style="left:201px;top:3459px" aria-hidden="true"></span>
<span class="abs copyright">© 2026 | quellbrookfillhouse.com</span>

</body>
</html>
```